We are a recruitment company based in Norwich/Cambridge England.
I have included our company logo which we want to remain the same.

What we are looking for is a new creative Business card which will really stand out!!

Contact Information for Business Card

Harriet Dunmore
email: Harriet@plavex.co.uk
Address: Brackwell House
Fenmoor Enterprise Park
Partridge Way
Norwich
QB9 3KX
Tel:01632 960418

```html
<!DOCTYPE html>
<html lang="en">
<head>
<meta charset="utf-8">
<title>Plavex Business Card</title>
<link href="https://fonts.googleapis.com/css2?family=Roboto:wght@400;500&display=swap" rel="stylesheet">
<style>
  :root {
    --backdrop: #2b2b2b;
    --card-white: #f4f4f4;
    --brand-green: #8cc542;
    --brand-grey: #8a8a8a;
    --ink: #454545;
    --white: #ffffff;
  }
  * { margin: 0; padding: 0; box-sizing: border-box; }
  html, body { width: 1200px; height: 960px; overflow: hidden; }
  body {
    background: var(--backdrop);
    font-family: "Roboto", Arial, sans-serif;
    position: relative;
  }
  .card {
    position: absolute;
    left: 320px;
    width: 600px;
    height: 345px;
    box-shadow: 0 4px 12px rgba(0,0,0,0.45);
  }
  .card-front { top: 103px; background: var(--card-white); }
  .card-back { top: 492px; background: var(--brand-green); }

  .side-band {
    position: absolute;
    left: 0; top: 0;
    width: 78px; height: 100%;
    background: var(--brand-green);
  }
  .brand {
    position: absolute;
    left: 32px; top: 58px;
    display: flex;
    align-items: center;
    gap: 12px;
  }
  .brand-dot {
    width: 46px; height: 46px;
    border-radius: 50%;
    background: var(--brand-green);
  }
  .brand-name {
    font-size: 40px;
    font-weight: 500;
    color: var(--brand-grey);
    letter-spacing: -0.5px;
  }
  .contact {
    position: absolute;
    right: 27px; top: 166px;
    text-align: right;
    color: var(--ink);
  }
  .person-name {
    font-size: 21px;
    font-weight: 500;
    color: var(--brand-green);
    line-height: 1.1;
  }
  .person-role {
    font-size: 15px;
    font-weight: 500;
    color: var(--brand-grey);
    margin-top: 2px;
  }
  .address {
    font-size: 14.5px;
    line-height: 18px;
    margin-top: 13px;
    margin-right: 3px;
  }
  .channels { list-style: none; margin-top: 9px; }
  .channels li {
    font-size: 14.5px;
    line-height: 19.5px;
    display: flex;
    justify-content: flex-end;
    align-items: center;
    gap: 7px;
  }
  .channels svg { width: 13px; height: 13px; fill: var(--brand-green); }

  .back-brand {
    position: absolute;
    left: 0; right: 0; top: 105px;
    display: flex;
    flex-direction: column;
    align-items: center;
    gap: 14px;
  }
  .back-dot {
    width: 70px; height: 70px;
    border-radius: 50%;
    background: var(--white);
  }
  .back-name {
    font-size: 44px;
    font-weight: 500;
    color: var(--white);
  }
  .back-web {
    position: absolute;
    left: 0; right: 0; bottom: 25px;
    text-align: center;
    color: var(--white);
    font-size: 14px;
    letter-spacing: 5px;
  }
</style>
</head>
<body>
  <section class="card card-front">
    <div class="side-band"></div>
    <div class="brand">
      <span class="brand-dot"></span>
      <span class="brand-name">Plavex</span>
    </div>
    <div class="contact">
      <p class="person-name">HARRIET DUNMORE</p>
      <p class="person-role">CEO/FOUNDER</p>
      <p class="address">Brackwell House<br>Partridge Way, QB9 3KX</p>
      <ul class="channels">
        <li>01632 960418
          <svg viewBox="0 0 24 24" aria-hidden="true"><path d="M6.6 10.8c1.4 2.8 3.8 5.1 6.6 6.6l2.2-2.2c.3-.3.7-.4 1-.2 1.1.4 2.3.6 3.6.6.6 0 1 .4 1 1V20c0 .6-.4 1-1 1C10.6 21 3 13.4 3 4c0-.6.4-1 1-1h3.5c.6 0 1 .4 1 1 0 1.3.2 2.5.6 3.6.1.3 0 .7-.2 1z"/></svg>
        </li>
        <li>Harriet@plavex.co.uk
          <svg viewBox="0 0 24 24" aria-hidden="true"><path d="M2 5h20v14H2z M2 5l10 8 10-8" fill="var(--brand-green)"/><path d="M3 6l9 7 9-7" fill="none" stroke="#f4f4f4" stroke-width="1.6"/></svg>
        </li>
        <li>www.plavex.co.uk
          <svg viewBox="0 0 24 24" aria-hidden="true"><circle cx="12" cy="12" r="10"/></svg>
        </li>
      </ul>
    </div>
  </section>

  <section class="card card-back">
    <div class="back-brand">
      <span class="back-dot"></span>
      <span class="back-name">Plavex</span>
    </div>
    <p class="back-web">www.plavex.co.uk</p>
  </section>
</body>
</html>
```